KBT Business Cards

We require business cards for our business. We would like a matte black back to the card, with our logo centred in the middle. The front side of the card is open to design.

Target Market(s)

Clients looking for legal services (professional)

Industry/Entity Type

Legal

Contact Information for Business Card

Doran Kelbrath
Partner
Mobile: 0461 738 524
Email: doran@kbtlaw.co
Website: www.kbtlaw.co
Level 3, 118 Wendmore Street
Sydney NSW 2000

Font styles to use
Other font styles liked:
• Avenir

Colors
f04a50
ffffff
1b1b1b

Requirements
Must have
• Black back with logo included in the centre of the card.
• Our font is Avenir.

```html
<!DOCTYPE html>
<html lang="en">
<head>
<meta charset="utf-8">
<title>Kelbrath Bower Legal – Business Card</title>
<link rel="stylesheet" href="https://fonts.googleapis.com/css2?family=Nunito+Sans:wght@400;600;700&display=swap">
<style>
  :root {
    --crimson: #bc0b3e;
    --ink: #1b1b1b;
    --paper: #ffffff;
    --matte: #121314;
    --matte-mark: #2a2c2e;
    --stage: #e9e8e6;
  }
  * { margin: 0; padding: 0; box-sizing: border-box; }
  html, body { width: 1200px; height: 844px; overflow: hidden; }
  body {
    background: var(--stage);
    font-family: "Nunito Sans", "Avenir", sans-serif;
    position: relative;
  }
  .card {
    position: absolute;
    top: 257px;
    width: 540px;
    height: 329px;
    overflow: hidden;
    box-shadow: 0 6px 18px rgba(0,0,0,.18);
  }
  .card--front { left: 40px; background: var(--paper); color: var(--ink); }
  .card--back { left: 620px; background: var(--matte); }

  .brand {
    position: absolute;
    display: flex;
    align-items: center;
    gap: 10px;
    font-weight: 700;
    text-transform: uppercase;
    line-height: 1;
  }
  .card--front .brand { top: 62px; right: 58px; color: var(--ink); font-size: 17px; letter-spacing: .5px; }
  .brand__square { width: 22px; height: 22px; background: var(--crimson); }
  .brand__name { display: flex; flex-direction: column; gap: 3px; }

  .person { position: absolute; left: 44px; top: 168px; }
  .person__name { color: var(--crimson); font-size: 26px; font-weight: 600; line-height: 1; }
  .person__role { font-size: 15px; font-weight: 600; line-height: 1; margin-top: 10px; margin-left: 4px; }
  .rule {
    position: absolute; left: 118px; right: 52px; top: 202px;
    height: 1.5px; background: var(--crimson);
  }
  .contact { position: absolute; left: 48px; top: 226px; list-style: none; font-size: 13.5px; line-height: 1.3; }
  .contact li { display: flex; align-items: center; gap: 9px; margin-bottom: 3px; }
  .contact svg { width: 13px; height: 13px; fill: var(--crimson); }

  .address {
    position: absolute; right: 52px; top: 212px;
    text-align: right; font-size: 13px; line-height: 1.35;
  }
  .footer-bands { position: absolute; left: 0; bottom: 0; width: 540px; height: 82px; }
  .website {
    position: absolute; right: 70px; bottom: 36px;
    color: var(--paper); font-size: 13px; font-weight: 600;
  }

  .card--back .brand {
    top: 50%; left: 50%; transform: translate(-50%, -62%);
    color: var(--matte-mark); font-size: 24px; letter-spacing: .6px; gap: 14px;
  }
  .card--back .brand__square { width: 30px; height: 30px; background: var(--matte-mark); }
  .back-website {
    position: absolute; left: 0; right: 0; top: 222px;
    text-align: center; color: var(--crimson); font-size: 11px; letter-spacing: 1.5px;
  }
</style>
</head>
<body>

<section class="card card--front" aria-label="Business card front">
  <div class="brand">
    <span class="brand__square"></span>
    <span class="brand__name"><span>Kelbrath</span><span>Bower</span><span>Legal</span></span>
  </div>

  <div class="person">
    <p class="person__name">Doran Kelbrath</p>
    <p class="person__role">Partner</p>
  </div>
  <div class="rule"></div>

  <ul class="contact">
    <li>
      <svg viewBox="0 0 24 24" aria-hidden="true"><path d="M6.6 10.8a15.1 15.1 0 0 0 6.6 6.6l2.2-2.2a1 1 0 0 1 1-.25 11.4 11.4 0 0 0 3.6.57 1 1 0 0 1 1 1V20a1 1 0 0 1-1 1A17 17 0 0 1 3 4a1 1 0 0 1 1-1h3.5a1 1 0 0 1 1 1c0 1.250.2 2.45.57 3.57a1 1 0 0 1-.25 1z"/></svg>
      <span>0461 738 524</span>
    </li>
    <li>
      <svg viewBox="0 0 24 24" aria-hidden="true"><path d="M2 5h20v14H2zm2 2v.5l8 5 8-5V7zm0 2.9V17h16V9.9l-8 5z"/></svg>
      <span>doran@kbtlaw.co</span>
    </li>
  </ul>

  <p class="address">Level 3, 118 Wendmore<br>Street Sydney NSW 2000</p>

  <svg class="footer-bands" viewBox="0 0 540 82" aria-hidden="true">
    <polygon points="0,38 360,38 353,64 0,64" fill="var(--crimson)"/>
    <polygon points="366,10 506,10 500,52 358,52" fill="var(--ink)"/>
    <polygon points="512,10 540,10 540,34 508,34" fill="var(--crimson)"/>
  </svg>
  <p class="website">www.kbtlaw.co</p>
</section>

<section class="card card--back" aria-label="Business card back">
  <div class="brand">
    <span class="brand__square"></span>
    <span class="brand__name"><span>Kelbrath</span><span>Bower</span><span>Legal</span></span>
  </div>
  <p class="back-website">www.kbtlaw.co</p>
</section>

</body>
</html>
```